Fine Art business needs new website

We need a simple website with a home page, about us page, New sculptures, Sold sculptures, and a contact us page.Our sculptures are very high end one of a kind pieces. As such we need the site to be VERY elegant and professional. Lastly, because I'll be updating pictures on the website on a monthly basis it needs to be user friendly to update (Wordpress is preferred). The only branding we have so far for the business is a business card.
Updates
I wasn't completely ready when this project launched, also I am on the road right now and haven't been able to be as responsive to all you designers as I would like. I will work on giving feedback to all the top designs we've received so far. Thank you all so much for your participation and hardwork.
Target Market(s)
High end customers (affluent), art collectors, interior decorators/designers
Industry/Entity Type
Art Gallery
Coding
Coded - Design and coding required
Number of Pages Required
5+ page
Requirements
Must have
- Easily editable picture gallery for myself so that I can add new pieces(pictures of the pieces), remove sold pieces, etc. I would like the website to be built in wordpress so I can update it. I currently use mangewordpress through Netmarro for my other business website and would like to do the same for this one.
- Pages:
- -Intro page with featured pieces
- -Current pieces gallery (for sale) mainly a picture gallery
- -Sculptures archive (sold pieces) another picture gallery
- -About us: Pull-down of -about the artist (attached content)
- -Artistic Process (attached content)
- -Show Schedule:
- -one page dedicated to "friends of TMV" (basically a link page)
- TO BE CLEAR "www.pineroverslane.com" IS A TOTALLY DIFFERENT SITE AND I'M NOT TRYING TO COMBINE THE TWO OR JOIN THEM INTO ONE. This page needs be more elegant and seperate from the Pine Rovers site.
- UPDATE: I'd like a link to the TMV Faceplume page: https://www.faceplume-social.com/mirelcraftworks/
Nice to have
- I would like the pictures on the gallery pages able to have text connected with them (Materials, price)
- I would like the site style and fonts to be similar to our business cards we've already had designed (picture attached).
Should not have
- Too much flash or other things that will make the site slow to load.

```html
<!DOCTYPE html>
<html lang="en">
<head>
<meta charset="utf-8">
<title>Tamarack Vale Studios</title>
<link rel="stylesheet" href="https://fonts.googleapis.com/css2?family=Poppins:wght@500;600;800;900&family=Open+Sans:wght@400;600;700&family=Montserrat:wght@500;700&display=swap">
<style>
:root{
  --purple:#2b0f47;
  --purple-deep:#250c3e;
  --ink:#222;
  --muted:#444;
  --paper:#ffffff;
  --mist:#f4f0f0;
  --line:#3c2359;
}
*{margin:0;padding:0;box-sizing:border-box}
html,body{width:1200px;height:2848px;overflow:hidden;background:var(--paper)}
body{position:relative;font-family:"Open Sans",sans-serif;color:var(--ink)}
.abs{position:absolute}

/* header */
.site-header{left:0;top:0;width:1200px;height:68px;background:var(--paper)}
.brand-box{left:131px;top:0;width:275px;height:152px;background:var(--paper);z-index:3;box-shadow:0 2px 8px rgba(0,0,0,.15);display:flex;align-items:flex-end;justify-content:center;padding-bottom:14px}
.brand-box .brand-name{font-family:"Open Sans",sans-serif;font-weight:400;font-size:14px;letter-spacing:2px;color:#555}
.brand-box .brand-band{position:absolute;left:0;top:0;width:275px;height:100px;background:linear-gradient(135deg,#3a1d6b,#6a3fa8 55%,#2b1548)}
.main-nav{right:131px;top:25px;display:flex;gap:24px;align-items:center}
.main-nav a{font-family:"Poppins",sans-serif;font-weight:500;font-size:12.5px;color:#111;text-decoration:none;text-transform:uppercase;line-height:24px}
.main-nav a.active{background:var(--purple);color:#fff;padding:0 10px}

/* hero */
.hero{left:0;top:68px;width:1200px;height:638px;background:radial-gradient(ellipse at 30% 40%,#c9b9a4 0%,#8a7462 40%,#4a3a30 75%,#2b241f 100%)}
.hero-title{left:0;top:325px;width:1200px;text-align:center;font-family:"Poppins",sans-serif;font-weight:900;font-size:52px;color:#fff;text-shadow:0 2px 6px rgba(0,0,0,.35)}
.btn{display:flex;align-items:center;justify-content:center;background:var(--purple);color:#fff;font-family:"Poppins",sans-serif;font-weight:800;text-transform:uppercase;text-decoration:none}
.hero-btn{left:522px;top:420px;width:156px;height:47px;font-size:17px}
.hero-dots{left:542px;top:643px;display:flex;gap:11px}
.hero-dots span{width:12px;height:12px;border-radius:50%;background:rgba(255,255,255,.85)}
.hero-dots span.on{background:#222;border:3px solid #fff}
.hero-dots span.dim{background:rgba(255,255,255,.3)}

/* welcome */
.mist-band{left:0;top:1206px;width:1200px;height:741px;background:var(--mist)}
.welcome-photo{left:158px;top:769px;width:383px;height:511px;background:radial-gradient(ellipse at 50% 40%,#4e3a8a 0%,#2a1d45 30%,#121012 60%,#0d0d0d 100%)}
.welcome-kicker{left:612px;top:790px;font-family:"Poppins",sans-serif;font-weight:500;font-size:23px;color:#222}
.welcome-title{left:612px;top:820px;font-family:"Poppins",sans-serif;font-weight:900;font-size:41px;color:var(--purple)}
.rule{width:70px;height:8px}
.rule::before,.rule::after{content:"";position:absolute;height:2px;background:var(--line)}
.rule::before{left:0;top:0;width:50px}
.rule::after{left:20px;top:6px;width:50px}
.welcome-rule{left:619px;top:882px}
.welcome-text{left:617px;top:932px;width:400px;font-size:15.5px;line-height:21px;color:#333}
.welcome-btn{left:619px;top:1100px;width:124px;height:38px;font-size:13px}

/* sections */
.section-title{left:0;width:1200px;text-align:center;font-family:"Poppins",sans-serif;font-weight:800;font-size:29px;color:var(--purple)}
.section-rule{left:565px}
.product{width:222px;height:378px;background:#fff}
.product .shot{height:301px}
.product .name{position:absolute;left:21px;top:316px;font-family:"Montserrat",sans-serif;font-weight:500;font-size:18px;color:#222}
.product .price{position:absolute;left:21px;top:340px;font-family:"Montserrat",sans-serif;font-weight:700;font-size:19px;color:var(--purple)}
.chev{width:22px;height:34px}

.purple-band{left:0;top:2302px;width:1200px;height:546px;background:var(--purple-deep)}
.gallery-shot{width:222px}
.round-arrow{width:36px;height:36px}

/* footer */
.foot-brand{left:131px;top:2526px;width:275px;height:149px;background:#fff;display:flex;align-items:flex-end;justify-content:center;padding-bottom:14px}
.foot-brand .brand-band{position:absolute;left:0;top:0;width:275px;height:96px;background:linear-gradient(135deg,#3a1d6b,#6a3fa8 55%,#2b1548)}
.foot-brand .brand-name{font-size:14px;letter-spacing:2px;color:#555}
.foot-head{font-family:"Open Sans",sans-serif;font-weight:700;font-size:12.5px;color:#fff;text-transform:uppercase}
.foot-text{font-size:11.5px;line-height:17px;color:#e8e2f0}
.foot-row{display:flex;gap:14px;align-items:flex-start}
.foot-menu{list-style:none}
.foot-menu li{font-size:11.5px;line-height:17.5px;color:#e8e2f0}
.social{display:flex;align-items:center;gap:12px;font-size:11.5px;color:#e8e2f0;height:30px}
.social .dot{width:28px;height:28px;border-radius:50%;background:#1f6fc9}
.social .dot.light{background:#2ea6e6}
.social .dot.none{background:transparent;border:1px solid rgba(255,255,255,.4)}
.foot-divider{left:124px;top:2748px;width:952px;height:1px;background:rgba(255,255,255,.14)}
.copyright{left:0;top:2795px;width:1200px;text-align:center;font-size:11.5px;color:#e8e2f0}
</style>
</head>
<body>

<header class="site-header abs"></header>
<div class="brand-box abs">
  <div class="brand-band" role="img" aria-label="Amethyst crystal cluster banner"></div>
  <span class="brand-name">TAMARACK VALE STUDIOS</span>
</div>
<nav class="main-nav abs">
  <a class="active" href="#">Home</a>
  <a href="#">About us</a>
  <a href="#">New sculptures</a>
  <a href="#">Sold sculptures</a>
  <a href="#">Contact us</a>
</nav>

<section class="hero abs" role="img" aria-label="Polished agate and jasper stones laid on linen"></section>
<h1 class="hero-title abs">TAMARACK VALE STUDIOS</h1>
<a class="btn hero-btn abs" href="#">Read more</a>
<div class="hero-dots abs"><span></span><span></span><span class="on"></span><span class="dim"></span><span class="dim"></span></div>

<div class="mist-band abs"></div>
<div class="welcome-photo abs" role="img" aria-label="Amethyst geode sculpture on a brass stand"></div>
<p class="welcome-kicker abs">WELCOME TO</p>
<h2 class="welcome-title abs">TAMARACK VALE STUDIOS</h2>
<div class="rule welcome-rule abs"></div>
<p class="welcome-text abs">The Pine Rovers or known to some as the “Ember Shell Guys” originally began 20 years ago when the founder of “Ember Bones” and the “Ember Shells”, Hollis Brenner, traded an old man one of his signature mineral sculptures for a peculiar looking machine that supposedly was made specifically to crack geodes!</p>
<a class="btn welcome-btn abs" href="#">Read more</a>

<h2 class="section-title abs" style="top:1366px">FEATURED PRODUCTS</h2>
<div class="rule section-rule abs" style="top:1420px"></div>

<svg class="chev abs" style="left:70px;top:1641px" viewBox="0 0 22 34"><path d="M16 4 L5 17 L16 30" fill="none" stroke="#999" stroke-width="3"/></svg>
<svg class="chev abs" style="left:1104px;top:1641px" viewBox="0 0 22 34"><path d="M6 4 L17 17 L6 30" fill="none" stroke="#999" stroke-width="3"/></svg>

<article class="product abs" style="left:133px;top:1499px">
  <div class="shot" role="img" aria-label="Green malachite sculpture on black" style="background:radial-gradient(ellipse at 50% 45%,#2f6a4a 0%,#143022 30%,#0d0d0d 65%)"></div>
  <p class="name">Ridge Geodes</p><p class="price">$ 4.00</p>
</article>
<article class="product abs" style="left:370px;top:1499px">
  <div class="shot" role="img" aria-label="Twisted blue crystal sculpture on black" style="background:radial-gradient(ellipse at 50% 45%,#3a4f8e 0%,#1a2040 30%,#0d0d0d 65%)"></div>
  <p class="name">Ridge Geodes</p><p class="price">$ 4.00</p>
</article>
<article class="product abs" style="left:608px;top:1499px">
  <div class="shot" role="img" aria-label="Glowing amber agate slice sculpture on black" style="background:radial-gradient(ellipse at 50% 45%,#8a4a20 0%,#3a1e10 30%,#0d0d0d 65%)"></div>
  <p class="name">Ridge Geodes</p><p class="price">$ 4.00</p>
</article>
<article class="product abs" style="left:845px;top:1499px">
  <div class="shot" role="img" aria-label="Golden curved agate sculpture on black" style="background:radial-gradient(ellipse at 50% 40%,#b8761e 0%,#4a2a10 32%,#0d0d0d 65%)"></div>
  <p class="name">Ridge Geodes</p><p class="price">$ 4.00</p>
</article>

<div class="purple-band abs"></div>
<h2 class="section-title abs" style="top:2006px">GALLERY</h2>
<div class="rule section-rule abs" style="top:2060px"></div>

<div class="gallery-shot abs" style="left:131px;top:2152px;height:295px;background:radial-gradient(ellipse at 50% 45%,#6a4a38 0%,#2a1d18 32%,#0d0d0d 65%)" role="img" aria-label="Rough mineral sculpture with amethyst base"></div>
<div class="gallery-shot abs" style="left:370px;top:2177px;height:294px;background:radial-gradient(ellipse at 50% 45%,#b0602a 0%,#4a2410 32%,#0d0d0d 65%)" role="img" aria-label="Orange crystal geode on a stand"></div>
<div class="gallery-shot abs" style="left:606px;top:2152px;height:295px;background:radial-gradient(ellipse at 50% 45%,#c88430 0%,#4a2a10 30%,#0d0d0d 65%)" role="img" aria-label="Spiral ammonite and agate sculpture"></div>
<div class="gallery-shot abs" style="left:845px;top:2177px;height:294px;background:radial-gradient(ellipse at 50% 45%,#5a3a9a 0%,#2a1a45 32%,#0d0d0d 65%)" role="img" aria-label="Amethyst geode sculpture on wooden base"></div>

<svg class="round-arrow abs" style="left:64px;top:2286px" viewBox="0 0 36 36"><circle cx="18" cy="18" r="17" fill="#fff" stroke="#222" stroke-width="1.5"/><path d="M20.5 11 L13.5 18 L20.5 25" fill="none" stroke="#111" stroke-width="2.5"/></svg>
<svg class="round-arrow abs" style="left:1101px;top:2286px" viewBox="0 0 36 36"><circle cx="18" cy="18" r="17" fill="#fff" stroke="#222" stroke-width="1.5"/><path d="M15.5 11 L22.5 18 L15.5 25" fill="none" stroke="#111" stroke-width="2.5"/></svg>

<footer>
  <div class="foot-brand abs">
    <div class="brand-band" role="img" aria-label="Amethyst crystal cluster banner"></div>
    <span class="brand-name">TAMARACK VALE STUDIOS</span>
  </div>

  <div class="abs" style="left:503px;top:2530px">
    <p class="foot-head">Contact us</p>
    <div class="foot-row" style="margin-top:18px">
      <svg width="9" height="12" viewBox="0 0 9 12"><path d="M4.5 0C2 0 0 2 0 4.5 0 8 4.5 12 4.5 12S9 8 9 4.5C9 2 7 0 4.5 0z" fill="#fff"/><circle cx="4.5" cy="4.5" r="1.6" fill="var(--purple-deep)"/></svg>
      <p class="foot-text">PO box 550318<br>Cedar Hollow CO 80512</p>
    </div>
    <div class="foot-row" style="margin-top:15px">
      <svg width="11" height="11" viewBox="0 0 11 11"><path d="M2 0.5 L4 2.8 L3 4.2 C3.8 5.8 5.2 7.2 6.8 8 L8.2 7 L10.5 9 L9 10.7 C4.5 10.5 0.5 6.5 0.3 2Z" fill="#fff"/></svg>
      <p class="foot-text">555.014.2290</p>
    </div>
    <div class="foot-row" style="margin-top:17px">
      <svg width="12" height="9" viewBox="0 0 12 9"><rect width="12" height="9" fill="#fff"/><path d="M0 0 L6 5 L12 0" fill="none" stroke="var(--purple-deep)" stroke-width="1.2"/></svg>
      <p class="foot-text">hello@pineroverslane.com</p>
    </div>
  </div>

  <div class="abs" style="left:747px;top:2530px">
    <p class="foot-head">Menu</p>
    <ul class="foot-menu" style="margin-top:18px">
      <li>Home</li><li>About us</li><li>New sculptures</li><li>Sold sculptures</li><li>Contact us</li>
    </ul>
  </div>

  <div class="abs" style="left:931px;top:2530px">
    <p class="foot-head">Connect with us</p>
    <div style="margin-top:12px">
      <div class="social"><span class="dot"></span>Faceplume</div>
      <div class="social" style="margin-top:10px"><span class="dot light"></span>Chirpline</div>
      <div class="social" style="margin-top:10px"><span class="dot none"></span>Linkpost</div>
    </div>
  </div>

  <div class="foot-divider abs"></div>
  <p class="copyright abs">Copyrights @ 2018 All Rights Reserved</p>
</footer>

</body>
</html>
```